International Clinical Software Company needs a new business card design

We are looking for a new business card design for our company that has recently expanded into the UK market, making us a multinational company.
After having rebranded our website and produced a new style guide, we are looking for a business card that is creative and attention grabbing, while being consistent with the style and colour scheme used on the new website, www.plumvora.example
We produce care management technology for the aged care market, but the main aspect we aim to communicate is the human element of our software, and the way it assists in providing better care for aged people, and stronger relationships between aged people and the staff that care for them.
Our current business card is a dark green with gold text, which makes the text quite difficult to read, not very aesthetically appealing and the colour scheme looks quite dated.
We would like something fresh and modern, that can still be colourful but doesn't use large blocks of dark colour, and uses the colours within our logo.
Something tying in with the leaves that are used in our logo could work quite nicely, along with the Autumn/Fall colours of soft greens, yellows and reds (also in our existing logo). However also happy to look at fresh, completely out of the box ideas we may not have yet considered.
Target Market(s)
The people that receive this business card work in the aged card or health industry and are either corporate/management level staff or clinical (Registered Nurses, care workers etc.)
Industry/Entity Type
Health Product
Contact Information for Business Card
Company Name - BrindlewayCare
Company locations: United Kingdom, Australia, New Zealand
Staff Details:
Staff name: Derek Mallow
Staff job title: Executive Chairman
Staff email: d.mallow@plumvora.example
Office phone number: 01742 918576
Font styles to use
Other font styles liked:
- Calibri
Requirements
Must have
- Must include the BrindlewayCare brand name in it's current font
- Must include logo (3 leaves in gold circle)
- Must include Business Card Details
Nice to have
- Elements of gold
- White space
- Something autumn themed but not too cliched
Should not have
- No blue - used by a major competitor and we would like to differentiate from them
- Large blocks of dark green colour (the green that appears in our leaves on the logo on our current business card is the background colour and it is far too dark)

```html
<!DOCTYPE html>
<html lang="en">
<head>
<meta charset="utf-8">
<title>BrindlewayCare business card</title>
<link href="https://fonts.googleapis.com/css2?family=Open+Sans:wght@300;400;600;700&display=swap" rel="stylesheet">
<style>
  :root {
    --backdrop: #ebe7e1;
    --card-white: #ffffff;
    --card-back: #fbf8f3;
    --gold: #b49a6c;
    --crimson: #b41f3d;
    --ink: #3a3a3a;
    --ink-soft: #4a4a4a;
  }
  * { margin: 0; padding: 0; box-sizing: border-box; }
  html, body {
    width: 1200px;
    height: 900px;
    overflow: hidden;
    background: var(--backdrop);
    font-family: "Open Sans", Calibri, sans-serif;
  }
  .canvas { position: relative; width: 1200px; height: 900px; }

  .card {
    position: absolute;
    width: 580px;
    height: 332px;
    box-shadow: 0 6px 18px rgba(0,0,0,0.18);
    overflow: hidden;
  }

  /* Back of card */
  .card-back {
    left: 560px;
    top: 90px;
    background: var(--card-back);
    display: flex;
    align-items: center;
    justify-content: center;
  }
  .card-back .back-rule {
    position: absolute;
    left: 0;
    bottom: 0;
    width: 100%;
    height: 14px;
    background: var(--gold);
  }
  .card-back .back-rule::before {
    content: "";
    position: absolute;
    left: 0;
    top: -6px;
    width: 40%;
    height: 6px;
    background: var(--crimson);
  }
  .card-back .brand-name {
    color: var(--gold);
    font-weight: 300;
    font-size: 56px;
    letter-spacing: 1px;
  }

  /* Front of card */
  .card-front {
    left: 60px;
    top: 430px;
    background: var(--card-white);
  }
  .card-front .decor { position: absolute; left: 0; top: 0; }

  .person { position: absolute; left: 98px; top: 20px; }
  .person .name {
    font-weight: 700;
    font-size: 16px;
    line-height: 1.2;
  }
  .person .name .first { color: var(--gold); }
  .person .name .last { color: var(--crimson); }
  .person .title {
    color: var(--ink);
    font-size: 13.5px;
    line-height: 1.3;
  }

  .contact { position: absolute; left: 52px; top: 140px; color: var(--ink-soft); }
  .contact .line {
    display: flex;
    align-items: center;
    gap: 8px;
    font-size: 13.5px;
    line-height: 1.2;
    margin-left: 22px;
    margin-bottom: 6px;
  }
  .contact .line.email { margin-left: 41px; margin-bottom: 12px; }
  .contact .locations {
    font-size: 14.5px;
    line-height: 1.25;
    color: var(--ink);
  }

  .brand {
    position: absolute;
    left: 320px;
    top: 92px;
    width: 240px;
    display: flex;
    flex-direction: column;
    align-items: center;
    gap: 8px;
  }
  .brand .mark {
    width: 56px;
    height: 56px;
    border: 2px solid var(--gold);
    border-radius: 50%;
  }
  .brand .brand-name {
    color: var(--gold);
    font-weight: 300;
    font-size: 31px;
    letter-spacing: 0.5px;
  }
</style>
</head>
<body>
<main class="canvas">

  <section class="card card-back" aria-label="Card back">
    <span class="brand-name">BrindlewayCare</span>
    <span class="back-rule" aria-hidden="true"></span>
  </section>

  <section class="card card-front" aria-label="Card front">
    <svg class="decor" width="580" height="332" viewBox="0 0 580 332" aria-hidden="true">
      <polygon class="corner-red" points="0,0 30,0 14,20 0,20" fill="#b41f3d"/>
      <polygon class="corner-gold" points="40,0 78,0 78,34 14,34" fill="#b49a6c"/>
      <polygon class="band-red" points="0,236 300,262 290,276 0,250" fill="#b41f3d"/>
      <polygon class="band-gold" points="310,262 580,262 580,300 296,300" fill="#b49a6c"/>
    </svg>

    <div class="person">
      <div class="name"><span class="first">Derek</span> <span class="last">Mallow</span></div>
      <div class="title">Executive Chairman</div>
    </div>

    <div class="contact">
      <div class="line phone">
        <svg width="11" height="13" viewBox="0 0 24 24" aria-hidden="true">
          <path fill="#b49a6c" d="M6.6 10.8c1.4 2.8 3.8 5.1 6.6 6.6l2.2-2.2c.3-.3.7-.4 1-.2 1.1.4 2.3.6 3.6.6.6 0 1 .4 1 1V20c0 .6-.4 1-1 1C10.6 21 3 13.4 3 4c0-.6.4-1 1-1h3.5c.6 0 1 .4 1 1 0 1.3.2 2.5.6 3.6.1.3 0 .7-.2 1z"/>
        </svg>
        <span>01742 918576</span>
      </div>
      <div class="line email"><span>d.mallow@plumvora.example</span></div>
      <div class="locations">United Kingdom, Australia<br>New Zealand</div>
    </div>

    <div class="brand">
      <span class="mark" aria-hidden="true"></span>
      <span class="brand-name">BrindlewayCare</span>
    </div>
  </section>

</main>
</body>
</html>
```